Single-sided business card for restaurant velmora with new logo made on this site

Business card options with new logo including restaurant name, address, phone number and website. This business card is single-sided only and will be presented at the hostess desk for clients to take. I would like to see options based on a cream card background, a white card background, a yellow card background and a burgundy colored background. It needs to be elegant and traditional.

Target Market(s)

local and international crowd

Industry/Entity Type

restaurant

Contact Information for Business Card

address, website and phone number

Font styles to use
Serif

Colors
EE7325
F08F49
F5BC92
FAE3D3
FDF4ED

Requirements
Must have
• new logo, address, phone number, website
Should not have
• more than three colors

```html
<!DOCTYPE html>
<html lang="es">
<head>
<meta charset="utf-8">
<title>Velmora – Tarjeta de presentación</title>
<link rel="stylesheet" href="https://fonts.googleapis.com/css2?family=Tinos:wght@400;700&display=swap">
<style>
  :root {
    --backdrop: #c9c9c9;
    --card-cream: #fcebd1;
    --card-edge: #f0ae35;
    --accent-gold: #f0ae35;
    --leaf-tone: #e6d5b6;
    --ink-brown: #2e1a14;
  }
  * { margin: 0; padding: 0; box-sizing: border-box; }
  html, body {
    width: 1200px; height: 800px; overflow: hidden;
    background: var(--backdrop);
  }
  .canvas {
    position: relative; width: 1200px; height: 800px;
    display: flex; align-items: center; justify-content: center;
  }
  .business-card {
    position: relative;
    width: 1000px; height: 580px;
    background: var(--card-cream);
    border-radius: 44px;
    border-bottom: 4px solid var(--card-edge);
    overflow: hidden;
    font-family: "Tinos", "Times New Roman", serif;
    color: var(--ink-brown);
  }
  .leaf-decoration {
    position: absolute; right: 0; top: 0;
    width: 560px; height: 100%;
    background: radial-gradient(ellipse at 70% 95%, var(--leaf-tone) 0%, rgba(230,213,182,0.7) 45%, rgba(252,235,209,0) 78%);
  }
  .brand-block {
    position: absolute; left: 130px; top: 175px;
    width: 300px;
    display: flex; flex-direction: column; align-items: center;
  }
  .brand-square {
    width: 150px; height: 150px;
    background: var(--accent-gold);
  }
  .brand-name {
    margin-top: 26px;
    font-size: 46px; font-weight: 400;
    letter-spacing: 10px;
    color: var(--ink-brown);
  }
  .contact-block {
    position: absolute; left: 470px; top: 170px;
    font-size: 29px; line-height: 34px;
  }
  .contact-block .label { font-weight: 700; }
  .contact-block .address { margin-bottom: 14px; }
  .contact-block .reservations { margin-bottom: 20px; }
  .contact-block .phone { font-size: 32px; }
  .contact-block .website { font-weight: 700; font-size: 27px; letter-spacing: 1px; }
</style>
</head>
<body>
  <main class="canvas">
    <article class="business-card">
      <div class="leaf-decoration" role="img" aria-label="Faint large agave leaf decoration in soft beige tones"></div>

      <div class="brand-block">
        <div class="brand-square"></div>
        <div class="brand-name">VELMORA</div>
      </div>

      <section class="contact-block">
        <div class="address">
          <div class="label">Restaurant Velmora</div>
          <div>Jacarandá 415</div>
          <div>Bahías de Santa Lucía</div>
          <div>Oaxaca CP 70312</div>
        </div>
        <div class="reservations">
          <div class="label">Reservaciones</div>
          <div class="phone">958-412-0376</div>
        </div>
        <div class="website">www.velmora.com.mx</div>
      </section>
    </article>
  </main>
</body>
</html>
```